New Business card design to reflect rebrand

I would like a business card design with a good base colour for our new logo and also a placeholder for a profile pic of the card holder. the design needs to be editable to the point that we can easily change the picture of the person and use that design for printmerlo etc. we are looking at a metalic finish business card so will need a good base colour to bring out the finish.

Target Market(s)

prospective customers

Industry/Entity Type

Business

Contact Information for Business Card

I would like one editable design that we can change the name of the card holder and profile picture. The design need to be in a format that be send to printmerlo etc.

Our address is Fenwick Lodge, Copse Lane, Ashcombe Vale, GU14 3TP Tel no. 01483 556172

Requirements
Must have
• place holder for a profile pic for the card holder. in AI or preferably PSD format

```html
<!DOCTYPE html>
<html lang="en">
<head>
<meta charset="utf-8">
<title>Corvane Workplace Services – Business Card</title>
<link rel="stylesheet" href="https://fonts.googleapis.com/css2?family=Open+Sans:wght@400;600;700&display=swap">
<style>
  :root {
    --backdrop: #ececec;
    --card-white: #f7f7f7;
    --brand-orange: #e8620c;
    --brand-slate: #3f5069;
    --text-grey: #55585c;
    --photo-dark: #23283a;
    --photo-light: #dcdcdc;
  }
  * { margin: 0; padding: 0; box-sizing: border-box; }
  html, body {
    width: 1200px; height: 900px; overflow: hidden;
    background: var(--backdrop);
    font-family: "Open Sans", Arial, sans-serif;
  }
  .canvas {
    position: relative; width: 1200px; height: 900px;
    display: flex; align-items: center; justify-content: center; gap: 60px;
  }
  .card {
    position: relative; width: 510px; height: 316px;
    border-radius: 4px; overflow: hidden;
    box-shadow: 0 6px 18px rgba(0,0,0,0.12);
  }
  .card-front { background: var(--card-white); }
  .card-back {
    background: var(--brand-orange);
    display: flex; align-items: center; justify-content: center;
  }
  .front-wordmark {
    position: absolute; left: 40px; top: 40px;
    font-weight: 700; font-size: 40px; letter-spacing: 3px;
    color: var(--brand-slate);
  }
  .holder-name {
    position: absolute; left: 42px; top: 108px;
    font-size: 17px; font-weight: 600; letter-spacing: 2px; text-transform: uppercase;
  }
  .holder-name .first { color: var(--brand-orange); }
  .holder-name .last { color: var(--brand-slate); }
  .contact {
    position: absolute; left: 42px; top: 146px;
    font-size: 12px; line-height: 1.6; color: var(--text-grey); list-style: none;
  }
  .profile-photo {
    position: absolute; right: 0; bottom: 0; width: 250px; height: 170px;
    background: linear-gradient(180deg, var(--photo-light) 0%, #8a8f99 45%, var(--photo-dark) 100%);
  }
  .back-wordmark {
    text-align: center; color: #ffffff; font-weight: 700;
  }
  .back-wordmark .name { display: block; font-size: 46px; letter-spacing: 4px; text-transform: uppercase; }
  .back-wordmark .tagline { display: block; font-size: 17px; letter-spacing: 6px; text-transform: uppercase; margin-top: 2px; }
</style>
</head>
<body>
<main class="canvas">
  <section class="card card-front" aria-label="Business card front">
    <div class="front-wordmark">CORVANE</div>
    <h1 class="holder-name"><span class="first">Daniel</span> <span class="last">Harrow</span></h1>
    <ul class="contact">
      <li>01483 556172</li>
      <li>info@corvane.com</li>
      <li>Fenwick Lodge, Copse Lane,</li>
      <li>Ashcombe Vale, GU14 3TP</li>
    </ul>
    <div class="profile-photo" role="img" aria-label="Profile photo of the card holder in a dark suit"></div>
  </section>
  <section class="card card-back" aria-label="Business card back">
    <div class="back-wordmark">
      <span class="name">Corvane</span>
      <span class="tagline">Workplace Services</span>
    </div>
  </section>
</main>
</body>
</html>
```